4D Cradle Glimpse Luxury Ultrasound Billboard

Design a HIGH-END, MODERN billboard for my private prenatal ultrasound studio, 4D Cradle Glimpse, located in Pace, Florida.
This billboard will be viewed by drivers traveling at highway speeds, so it must be extremely clean, simple, and readable within 6 seconds.
About My Business
4D Cradle Glimpse is a private prenatal ultrasound studio specializing in:
Highest technology 4D/HD Ultrasounds
Early Gender Determination
Pregnancy Confirmation
I have been serving families for nearly 10 years and is known for creating a memorable experience, not just an ultrasound appointment.
Design Style
I DO NOT want:
Flowers
Leaves
Swirls
Glitter
Hearts everywhere
Busy backgrounds
Generic maternity stock graphics
I DO want:
Modern
Luxury
Upscale
Clean
Professional
Eye-catching
Premium medical spa feel
Colors
Use colors from my logo:
LOGO Green ( or a deep green)
Black
White
Soft Gold accents
Images:
Incorporate my professional headshot in a clean, modern way, logo, and the ultrasound images
Text
Keep wording minimal.
Primary Headline ( OPEN TO IDEAS) :
EXAMPLES ( WOULD RATHER SOMETHING MORE CATCHY)
" ADVANCED IMAGING. UNFORGETTABLE MOMENTS"
"MEET YOUR BABY BEFORE BIRTH"
Under headline:
4D Ultrasound • Early Gender • Pregnancy Confirmation
Business Name:
4D Cradle Glimpse
Private Prenatal Ultrasound Studio
Phone Number:
850-471-5923
Important
This billboard must be readable in 5–6 seconds from a moving vehicle.
Less text is better.
The phone number and business name must be visible from a distance.
The design should feel like a premium brand that immediately tells expecting parents:
“This is where I go to see my baby.”
Files Provided
Official logo
Headshot
Ultrasound images
Don’t make this look like a medical office billboard.
Make it look like a luxury baby experience billboard. That’s what separates 4D Cradle Glimpse from hospitals, OB offices, and all the new studios popping up around you. The emotional connection is what gets moms to book. ❤️
Billboard Size - 10.6” x 36”

```html
<!DOCTYPE html>
<html lang="en">
<head>
<meta charset="utf-8">
<title>4D Cradle Glimpse Billboard</title>
<link rel="stylesheet" href="https://fonts.googleapis.com/css2?family=Marcellus&family=Lato:wght@400;700&family=Libre+Baskerville:wght@700&display=swap">
<style>
  :root {
    --deep-green: #17432c;
    --green-dark: #0f3321;
    --gold: #c9a24c;
    --gold-light: #dcbb6a;
    --white: #ffffff;
    --stage: #f2f2f2;
    --skin-warm: #b5654a;
    --skin-glow: #d99677;
  }
  * { margin: 0; padding: 0; box-sizing: border-box; }
  html, body { width: 1200px; height: 805px; overflow: hidden; background: var(--stage); }
  .billboard {
    position: absolute; left: 0; top: 106px; width: 1200px; height: 592px;
    background: var(--deep-green); overflow: hidden;
  }
  .ultrasound-art {
    position: absolute; left: 18px; top: 100px; width: 490px; height: 492px;
    background: radial-gradient(ellipse 55% 48% at 50% 48%, var(--skin-glow) 0%, var(--skin-warm) 40%, rgba(120,60,40,0.55) 65%, rgba(23,67,44,0) 82%);
  }
  .headline {
    position: absolute; right: 287px; top: 40px; text-align: right;
    font-family: "Marcellus", serif; font-weight: 400; font-size: 86px; line-height: 86px;
    color: var(--gold); letter-spacing: 0.5px; white-space: nowrap;
  }
  .subhead {
    position: absolute; left: 515px; top: 230px;
    font-family: "Lato", sans-serif; font-weight: 400; font-size: 59px; line-height: 63px;
    color: var(--white); white-space: nowrap;
  }
  .services {
    position: absolute; left: 505px; top: 382px;
    font-family: "Lato", sans-serif; font-size: 23px; color: var(--white); white-space: nowrap;
  }
  .side-column {
    position: absolute; left: 936px; top: 0; width: 246px; height: 592px; background: var(--white);
  }
  .brand-name {
    position: absolute; left: 957px; top: 40px; width: 206px; text-align: center;
    font-family: "Lato", sans-serif; font-weight: 700; font-size: 31px; line-height: 36px;
    color: var(--deep-green);
  }
  .contact-panel {
    position: absolute; left: 503px; top: 436px; width: 697px; height: 156px;
    background: var(--white); border-top-left-radius: 22px; z-index: 1;
  }
  .phone {
    position: absolute; left: 32px; top: 28px;
    font-family: "Libre Baskerville", serif; font-weight: 700; font-size: 92px; line-height: 106px;
    letter-spacing: -1px; white-space: nowrap;
  }
  .phone .area { color: var(--deep-green); }
  .phone .number { color: var(--gold); }
  .headshot-frame {
    position: absolute; left: 948px; top: 160px; width: 222px; height: 298px;
    border: 4px solid var(--gold); background: var(--deep-green); padding: 4px; z-index: 2;
  }
  .headshot {
    width: 100%; height: 100%;
    background: linear-gradient(180deg, #2a5a3f 0%, #c9a97a 30%, #e4c9a4 55%, #2c5a40 80%, #e9e9e6 100%);
  }
</style>
</head>
<body>
  <section class="billboard">
    <div class="ultrasound-art" role="img" aria-label="4D ultrasound image of twin babies face to face"></div>
    <h1 class="headline">“THE MOMENT YOU<br>FALL IN LOVE.”</h1>
    <p class="subhead">See Your Baby<br>in Stunning 4D.</p>
    <p class="services">Early Gender • Pregnancy Confirmation</p>
    <div class="side-column"></div>
    <p class="brand-name">4D Cradle Glimpse</p>
    <div class="contact-panel">
      <p class="phone"><span class="area">850-</span><span class="number">471-5923</span></p>
    </div>
    <div class="headshot-frame">
      <div class="headshot" role="img" aria-label="Professional headshot of the studio owner"></div>
    </div>
  </section>
</body>
</html>
```